Retail Jewelry Business Card Design Project

We are in need of a new business card design for a retail jewelry store. This store is in the business of fine jewelry including but not specific to bridal jewelry, diamonds, designer jewelry and watches.

This store has been in business for 20 years but continues to strive for a modern professional appeal. The main colors use for this business are a royal blue, white and silver.

Target Market(s)

Target market is ages 18-50

Industry/Entity Type

Jewelry

Requirements
Must have
• Sales Person Name
Sales Person Email Address

Store Address
Store Phone
Website

Standard business card size. No odd shapes or sizes.
Nice to have
• Overall modern feel for card.

We have thought that a design with a nice feature of the logo on the back of the card would be nice but open to ideas.
Should not have
• No specific images of jewelry should be used.

```html
<!DOCTYPE html>
<html lang="en">
<head>
<meta charset="utf-8">
<title>Marlow Crane Fine Jewelry – Business Card</title>
<link rel="stylesheet" href="https://fonts.googleapis.com/css2?family=Tinos:ital,wght@0,400;1,400&display=swap">
<style>
  :root {
    --royal: #2e3190;
    --lilac: #7472b4;
    --white: #ffffff;
    --ink: #2a2a2a;
    --stage: #e9e9ee;
    --serif: "Tinos", "Times New Roman", serif;
  }
  * { box-sizing: border-box; margin: 0; padding: 0; }
  html, body { width: 1200px; height: 980px; overflow: hidden; }
  body {
    background: var(--stage);
    font-family: var(--serif);
    display: flex; flex-direction: column; align-items: center; justify-content: center;
    gap: 40px;
  }
  .card {
    position: relative;
    width: 760px; height: 434px;
    border-radius: 30px;
    overflow: hidden;
    box-shadow: 0 6px 18px rgba(0,0,0,.15);
  }
  /* Front */
  .card-front { background: var(--white); }
  .card-front .swoosh { position: absolute; inset: 0; width: 100%; height: 100%; }
  .brand {
    position: absolute; left: 54px; top: 52px;
    color: var(--royal); font-weight: 400; line-height: 1;
  }
  .brand .brand-name { font-size: 50px; display: block; }
  .brand .brand-tag { font-size: 24px; letter-spacing: 4px; text-transform: uppercase; display: block; margin-top: 10px; }
  .brand .brand-rule { display: block; width: 300px; height: 2px; background: var(--royal); margin-top: 10px; }
  .contacts {
    position: absolute; left: 54px; top: 232px;
    list-style: none; font-size: 17px; color: var(--ink);
  }
  .contacts li { display: flex; align-items: center; gap: 10px; margin-bottom: 8px; }
  .contacts svg { width: 15px; height: 15px; flex: none; }
  .divider {
    position: absolute; left: 300px; top: 330px;
    width: 1px; height: 64px; background: #9a9a9a;
  }
  .address {
    position: absolute; left: 318px; top: 336px;
    font-size: 18px; color: var(--ink); font-style: normal; line-height: 1.45;
  }
  .holder {
    position: absolute; right: 36px; top: 120px;
    font-size: 22px; font-style: italic; color: var(--white);
    white-space: nowrap;
  }
  /* Back */
  .card-back { background: var(--royal); color: var(--white); display: flex; flex-direction: column; align-items: center; justify-content: center; }
  .card-back .brand-name { font-size: 72px; line-height: 1; }
  .card-back .brand-rule { width: 440px; height: 2px; background: var(--white); margin-top: 12px; }
  .card-back .brand-tag { font-size: 32px; letter-spacing: 6px; text-transform: uppercase; margin-top: 12px; }
  .card-back .web { font-size: 20px; letter-spacing: 5px; margin-top: 36px; }
</style>
</head>
<body>

<section class="card card-front" aria-label="Business card front">
  <svg class="swoosh" viewBox="0 0 760 434" preserveAspectRatio="none" aria-hidden="true">
    <path d="M132 0 L760 0 L760 434 L572 434 C532 300 492 110 392 40 C312 -6 222 0 132 0 Z" fill="var(--lilac)"/>
    <path d="M146 0 L760 0 L760 434 L586 434 C546 300 506 110 406 40 C326 -6 236 0 146 0 Z" fill="var(--white)"/>
    <path d="M160 0 L760 0 L760 434 L600 434 C560 300 520 110 420 40 C340 -6 250 0 160 0 Z" fill="var(--royal)"/>
  </svg>

  <div class="brand">
    <span class="brand-name">Marlow Crane</span>
    <span class="brand-rule"></span>
    <span class="brand-tag">Fine Jewelry</span>
  </div>

  <ul class="contacts">
    <li><svg viewBox="0 0 16 16"><circle cx="8" cy="8" r="8" fill="var(--royal)"/><path d="M5 4.5l1.5-.5 1 2-1 .8a5 5 0 0 0 2.7 2.7l.8-1 2 1-.5 1.5c-3.5.3-6.8-3-6.5-6.5z" fill="#fff"/></svg>555-201-4388</li>
    <li><svg viewBox="0 0 16 16"><circle cx="8" cy="8" r="8" fill="var(--royal)"/><rect x="4" y="5" width="8" height="6" fill="#fff"/><path d="M4 5l4 3.5L12 5" fill="none" stroke="var(--royal)" stroke-width="1"/></svg>marlow@marlowcranejewelry.com</li>
    <li><svg viewBox="0 0 16 16"><circle cx="8" cy="8" r="8" fill="var(--royal)"/><circle cx="8" cy="8" r="4.5" fill="none" stroke="#fff" stroke-width="1"/><path d="M3.5 8h9M8 3.5v9" stroke="#fff" stroke-width="1"/></svg>www.marlowcranejewelry.com</li>
  </ul>

  <div class="divider"></div>
  <address class="address">2280 Lindell Avenue<br>Bayport, FL 32990</address>

  <p class="holder">Marlow Crane Ellison</p>
</section>

<section class="card card-back" aria-label="Business card back">
  <span class="brand-name">Marlow Crane</span>
  <span class="brand-rule"></span>
  <span class="brand-tag">Fine Jewelry</span>
  <span class="web">www.marlowcranejewelry.com</span>
</section>

</body>
</html>
```